CANNABIS BASED BUSINESS CARD DESIGN AND CREATION

WE ARE A PRIVATELY OWNED INVESTMENT CORPORATION. WE PRIMARILY INVEST IN LEGAL PUBLICALLY TRADED CANNABIS COMPANIES THAT ARE TRADED THROUGH THE OTC OR VOLTRIX. WE OFFER THE PUBLIC AN OPPORTUNITY TO PARTICIPATE DIRECTLY WITH THESE COMPANIES FOR NO FEES, NO COMMISSIONS AND IN DEPTH RESEARCH ON EVERY COMPANY PROFILE. WE ARE ALSO PRO FEDERAL LEGALIZATION AND WILL APPLY FOR CULTIVATION AND DISPENSARY LICENSES WHEN THEY BECOME AVAILABLE.

Target Market(s)

30-60 FEMALE AND MALE INVESTORS

Industry/Entity Type

Business

Contact Information for Business Card

EDS CAPITAL GROUP CORPERIN D SLAUGHTER(469) 426-6302ERIN@EDSCAPITALGROUP.COM

Font styles to use
Decorative

Requirements
Must have
• COMPANY LOGO
• CANNABIS LOGO
Nice to have
• MODERN FONT AND LOGOS

```html
<!DOCTYPE html>
<html lang="en">
<head>
<meta charset="utf-8">
<title>TQM Capital Group Corp – Business Card</title>
<link href="https://fonts.googleapis.com/css2?family=Lato:wght@400;700&display=swap" rel="stylesheet">
<style>
  :root {
    --backdrop: #6b7a1e;
    --card-black: #0a0a0a;
    --card-sheen: #242424;
    --leaf-green: #3db54a;
    --text-white: #f2f2f2;
    --text-grey: #a6a6a6;
    --rule-grey: #2e2e2e;
  }
  * { margin: 0; padding: 0; box-sizing: border-box; }
  html, body { width: 1200px; height: 900px; overflow: hidden; }
  body {
    background: var(--backdrop);
    font-family: "Lato", Arial, sans-serif;
    position: relative;
  }
  .card {
    position: absolute;
    width: 620px;
    height: 355px;
    background: radial-gradient(ellipse at 45% 35%, var(--card-sheen) 0%, var(--card-black) 62%);
    box-shadow: 0 10px 28px rgba(0,0,0,0.45);
    overflow: hidden;
  }
  .card--front { left: 70px; top: 70px; }
  .card--back { left: 510px; top: 475px; }

  /* Company name set as plain text: one colour, one weight */
  .brand {
    position: absolute;
    display: flex;
    flex-direction: column;
    align-items: center;
    color: var(--text-white);
    font-weight: 700;
    line-height: 1.1;
    text-align: center;
    white-space: nowrap;
  }
  .brand__dot {
    border-radius: 50%;
    background: var(--leaf-green);
  }
  .brand__short { letter-spacing: 2px; }
  .brand__rest { letter-spacing: 1px; }

  .card--front .brand {
    left: 50%; top: 50%;
    transform: translate(-50%, -50%);
    gap: 10px;
  }
  .card--front .brand__dot { width: 30px; height: 30px; }
  .card--front .brand__short { font-size: 54px; }
  .card--front .brand__rest { font-size: 24px; }

  .card--back .brand {
    right: 56px; top: 28px;
    gap: 6px;
  }
  .card--back .brand__dot { width: 18px; height: 18px; }
  .card--back .brand__short { font-size: 32px; }
  .card--back .brand__rest { font-size: 14px; }

  .back__rule {
    position: absolute;
    left: 40px; right: 40px; top: 170px;
    height: 1px;
    background: var(--rule-grey);
  }
  .holder {
    position: absolute;
    left: 40px; top: 250px;
    width: 250px;
    padding-bottom: 12px;
    border-bottom: 1px solid var(--rule-grey);
    color: var(--text-white);
    font-size: 16px;
    letter-spacing: 0.5px;
  }
  .contacts {
    position: absolute;
    right: 40px; top: 190px;
    list-style: none;
    color: var(--text-grey);
    font-size: 12.5px;
    line-height: 22px;
  }
  .contacts li { display: flex; align-items: center; gap: 10px; }
  .contacts svg { width: 13px; height: 13px; fill: var(--leaf-green); flex: none; }
</style>
</head>
<body>

  <section class="card card--front" aria-label="Card front">
    <div class="brand">
      <span class="brand__dot"></span>
      <span class="brand__short">TQM</span>
      <span class="brand__rest">Capital Group Corp</span>
    </div>
  </section>

  <section class="card card--back" aria-label="Card back">
    <div class="brand">
      <span class="brand__dot"></span>
      <span class="brand__short">TQM</span>
      <span class="brand__rest">Capital Group Corp</span>
    </div>
    <div class="back__rule"></div>
    <p class="holder">MARLA J PENDLEBURY</p>
    <ul class="contacts">
      <li>
        <svg viewBox="0 0 16 16" aria-hidden="true"><path d="M3 1l3 3-1.5 2a9 9 0 0 0 5.5 5.5L12 10l3 3-2 2C7 15 1 9 1 3z"/></svg>
        (555) 013-4478
      </li>
      <li>
        <svg viewBox="0 0 16 16" aria-hidden="true"><path d="M1 3h14v10H1z M1 3l7 6 7-6" stroke="#0a0a0a" stroke-width="1"/></svg>
        marla@tqmcapitalgroup-demo.com
      </li>
      <li>
        <svg viewBox="0 0 16 16" aria-hidden="true"><path d="M6 10l4-4M7 4l2-2a3 3 0 0 1 5 5l-2 2M9 12l-2 2a3 3 0 0 1-5-5l2-2" fill="none" stroke="#3db54a" stroke-width="2" stroke-linecap="round"/></svg>
        www.tqmcapitalgroup-demo.com
      </li>
    </ul>
  </section>

</body>
</html>
```